House flipping business web site needed

pinecrestholdingsgroup.example.
I am a residential developer in Northern NJ and I am looking for a fresh new updated website. I have an intro video about my company being made now. I don't update it very often but I want an easy format that I can add update photos to on projects I have worked on or homes I renovate for sale.

Target Market(s)

investors into my projects so a portfolio , people looking to sell their homes to me.

Industry/Entity Type

Real Estate Development

Number of Pages Required

4 page

Font styles to use
Serif

Colors
33b8a4
39a9d7
cadf82

Requirements
Must have
• space for an intro video about my company
• a portfolio with pictures and information about each project
• Markets we serve- Morris County, NJ
• My logo- already created
• SEO
• Yes I would like this to function over all platforms. Phone, computer, all platforms.
• history and background page
• I am looking for a completed page that I can upload to the site that hosts my website
Nice to have
• I want something creative, easy to navigate. modern.

```html
<!DOCTYPE html>
<html lang="en">
<head>
<meta charset="utf-8">
<title>Pinecrest Holdings Group</title>
<link rel="stylesheet" href="https://fonts.googleapis.com/css2?family=Playfair+Display:wght@400&family=Raleway:wght@400;500&family=Open+Sans:wght@400&display=swap">
<style>
:root{
  --teal:#17999b;
  --ink:#333333;
  --muted:#555555;
  --white:#ffffff;
  --frame:#c8c8c8;
  --footer:#4b4b4b;
  --footer-bar:#1f1f1f;
  --hero-a:#5b5d55;
  --hero-b:#2f3a2a;
}
*{margin:0;padding:0;box-sizing:border-box}
html,body{width:710px;height:1200px;overflow:hidden;background:var(--white)}
body{position:relative;font-family:'Open Sans',sans-serif;color:var(--ink)}
a{color:inherit;text-decoration:none}
h1,h2,h3,h4{font-weight:400}
.abs{position:absolute}

/* header */
.brand{left:46px;top:8px;width:88px;height:72px;display:flex;align-items:center;gap:5px}
.brand-mark{width:10px;height:10px;background:var(--teal);flex:none}
.brand-name{font-family:'Raleway',sans-serif;font-weight:500;font-size:12px;line-height:1.15;color:var(--teal)}
.social{left:252px;top:9px;display:flex;gap:31px}
.social span{width:12px;height:12px;border-radius:50%;background:#555}
.contact-top{left:476px;top:9px;display:flex;align-items:center;gap:10px;font-family:'Raleway',sans-serif;font-size:12px}
.contact-top .label{color:var(--teal);margin-right:2px}
.contact-top .num{color:#444}
.nav{left:395px;top:47px;display:flex;align-items:center;gap:22px;font-family:'Raleway',sans-serif;font-size:11.5px;color:#222}
.nav .active{color:var(--teal);border:1px solid var(--teal);border-radius:14px;padding:6px 11px}

/* hero */
.hero{left:0;top:87px;width:710px;height:339px;background:linear-gradient(180deg,var(--hero-a) 0%,#4d4f46 55%,var(--hero-b) 100%)}
.hero-title{left:47px;top:156px;font-family:'Playfair Display',serif;font-weight:400;font-size:29px;line-height:1.15;color:var(--white);letter-spacing:.5px}
.hero-sub{left:47px;top:234px;width:240px;font-size:11px;line-height:1.4;color:var(--white)}
.hero-btn{left:46px;top:294px;width:108px;height:31px;background:var(--white);border-radius:4px;display:flex;align-items:center;justify-content:center;font-family:'Raleway',sans-serif;font-weight:500;font-size:11.5px;color:var(--teal)}

/* gallery */
.section-title{left:0;width:710px;top:455px;text-align:center;font-family:'Raleway',sans-serif;font-weight:400;font-size:21px;color:var(--ink)}
.section-title em{font-style:normal;color:var(--teal)}
.title-rule{left:277px;top:481px;width:140px;height:1px;background:#777}
.card{top:501px;width:191px}
.card .photo{height:122px;border:6px solid var(--frame)}
.card h3{margin:9px 0 0 2px;font-family:'Raleway',sans-serif;font-size:12px;color:#444}
.card p{margin:6px 0 0 2px;font-size:9.5px;line-height:1.55;color:#333}
.more{display:flex;align-items:center;gap:7px;font-family:'Raleway',sans-serif;font-size:9.5px;color:var(--teal)}
.card .more{margin:5px 0 0 2px}

/* welcome */
.welcome-h{left:47px;top:752px;font-family:'Raleway',sans-serif;font-weight:400;font-size:22px;line-height:1.28;color:var(--ink)}
.welcome-h em{font-style:normal;color:var(--teal)}
.welcome-copy{left:47px;top:817px;width:330px;font-size:9px;line-height:1.6;color:var(--muted)}
.welcome-copy p+p{margin-top:11px}
.welcome-more{left:47px;top:922px}
.video{left:418px;top:770px;width:247px;height:136px;border:6px solid #666;background:linear-gradient(135deg,#8a8377,#5e6a4a 60%,#4f6b3c)}
.play{position:absolute;left:50%;top:50%;transform:translate(-50%,-50%)}

/* footer */
.wave{left:0;top:955px}
.footer{left:0;top:978px;width:710px;height:192px;background:var(--footer);color:var(--white)}
.f-col{top:1002px;color:var(--white)}
.f-col h4{font-family:'Raleway',sans-serif;font-size:11px;margin-bottom:16px}
.links li{list-style:none;font-size:9px;margin-bottom:21px}
.links li.current{color:var(--teal)}
.post{display:flex;gap:6px;margin-bottom:25px}
.post .thumb{width:38px;height:35px;background:linear-gradient(135deg,#6b7d8e,#3c4450)}
.post p{font-size:9px;line-height:1.3}
.news p{font-size:9px;line-height:1.3}
.news .date{color:var(--teal);font-size:8.5px}
.news .more{color:var(--white);margin:8px 0 0;font-size:9px}
.news hr{border:0;border-top:1px solid #ddd;width:107px;margin:5px 0 10px}
.reach li{list-style:none;display:flex;gap:11px;font-size:9px;line-height:1.4;margin-bottom:13px;align-items:flex-start}
.reach svg{flex:none;margin-top:1px}
.bottom-bar{left:0;top:1170px;width:710px;height:30px;background:var(--footer-bar);display:flex;align-items:center;justify-content:center;font-size:9px;color:var(--white)}
.bottom-bar span{color:var(--teal)}
</style>
</head>
<body>

<header>
  <a class="abs brand" href="#"><span class="brand-mark"></span><span class="brand-name">Pinecrest Holdings Group</span></a>
  <div class="abs social" aria-label="Social links"><span></span><span></span><span></span></div>
  <div class="abs contact-top">
    <span class="label">CONTANT US</span>
    <svg width="25" height="25" viewBox="0 0 25 25"><circle cx="12.5" cy="12.5" r="11.5" fill="none" stroke="#555" stroke-width="1"/><path d="M9 7l2 .3 1 3-1.4 1.2a8 8 0 003.6 3.6l1.2-1.4 3 1 .3 2-1.6 1.4C12 17.8 7.2 13 7.6 8.6z" fill="#555"/></svg>
    <span class="num">555-014-2290</span>
  </div>
  <nav class="abs nav">
    <a class="active" href="#">HOME</a><a href="#">ABOUT</a><a href="#">CONTACT</a><a href="#">PORTFOLIYO</a>
  </nav>
</header>

<section>
  <div class="abs hero" role="img" aria-label="Large two-storey stone family house with a green lawn at dusk"></div>
  <h1 class="abs hero-title">PINECREST<br>HOLDINGS GROUP</h1>
  <p class="abs hero-sub">We bring excellence to the home buying and renovation business.</p>
  <a class="abs hero-btn" href="#">READ MORE</a>
</section>

<section>
  <h2 class="abs section-title"><em>OUR</em> GALLERY</h2>
  <div class="abs title-rule"></div>

  <article class="abs card" style="left:46px">
    <div class="photo" role="img" aria-label="Modern white villa with pool at sunset" style="background:linear-gradient(180deg,#6d93bd 0%,#c9b79a 55%,#7a6248 100%)"></div>
    <h3>Project Title</h3>
    <p>Lorem Ipsum is simply dummy text of the printing and typesetting industry.</p>
    <a class="more" href="#">KNOW MORE <svg width="14" height="14" viewBox="0 0 14 14"><circle cx="7" cy="7" r="6.3" fill="none" stroke="currentColor"/><path d="M6 4l3 3-3 3" fill="none" stroke="currentColor"/></svg></a>
  </article>

  <article class="abs card" style="left:260px">
    <div class="photo" role="img" aria-label="Bright bedroom terrace overlooking the sea" style="background:linear-gradient(160deg,#e8e2d6 0%,#3f78b8 45%,#6d6a58 100%)"></div>
    <h3>Project Title</h3>
    <p>Lorem Ipsum is simply dummy text of the printing and typesetting industry.</p>
    <a class="more" href="#">KNOW MORE <svg width="14" height="14" viewBox="0 0 14 14"><circle cx="7" cy="7" r="6.3" fill="none" stroke="currentColor"/><path d="M6 4l3 3-3 3" fill="none" stroke="currentColor"/></svg></a>
  </article>

  <article class="abs card" style="left:474px">
    <div class="photo" role="img" aria-label="White coastal house with red shutters under blue sky" style="background:linear-gradient(180deg,#3f72c0 0%,#c9d3dc 55%,#7f9d4c 100%)"></div>
    <h3>Project Title</h3>
    <p>Lorem Ipsum is simply dummy text of the printing and typesetting industry.</p>
    <a class="more" href="#">KNOW MORE <svg width="14" height="14" viewBox="0 0 14 14"><circle cx="7" cy="7" r="6.3" fill="none" stroke="currentColor"/><path d="M6 4l3 3-3 3" fill="none" stroke="currentColor"/></svg></a>
  </article>
</section>

<section>
  <h2 class="abs welcome-h"><em>WELCOME TO</em><br>PINECREST HOLDINGS GROUP</h2>
  <div class="abs welcome-copy">
    <p>Pinecrest Holdings Group is a family run business with 3rd generation builders and renovators in the Morris County area.</p>
    <p>At Pinecrest Holdings Group we have a valuable support system and a team of investors, realtors, attorneys, contractors and property managers providing a combined package offering years of experience in the local market.</p>
  </div>
  <a class="abs more welcome-more" href="#">READ MORE <svg width="14" height="14" viewBox="0 0 14 14"><circle cx="7" cy="7" r="6.3" fill="none" stroke="currentColor"/><path d="M6 4l3 3-3 3" fill="none" stroke="currentColor"/></svg></a>
  <div class="abs video" role="img" aria-label="Intro video: family with their dog on a front lawn">
    <svg class="play" width="30" height="30" viewBox="0 0 30 30"><circle cx="15" cy="15" r="13.5" fill="none" stroke="#ffffff" stroke-width="1.5"/><path d="M12 9.5l8 5.5-8 5.5z" fill="#ffffff"/></svg>
  </div>
</section>

<footer>
  <svg class="abs wave" width="710" height="30" viewBox="0 0 710 30">
    <path d="M0 30 Q355 -14 710 30 L710 30 Z" fill="var(--footer)"/>
    <path d="M0 22 Q355 -18 710 22" fill="none" stroke="var(--teal)" stroke-width="4"/>
  </svg>
  <div class="abs footer"></div>

  <div class="abs f-col" style="left:48px">
    <h4>Useful Links</h4>
    <ul class="links"><li class="current">Home</li><li>About</li><li>Contact</li><li>Portfoliyo</li></ul>
  </div>

  <div class="abs f-col" style="left:146px;width:160px">
    <h4>BLOG POST</h4>
    <div class="post"><div class="thumb" role="img" aria-label="Author portrait"></div><p>Lorem Ipsum is simply<br>dummy text of<br>Today 5:60 pm-12.06.2016</p></div>
    <div class="post"><div class="thumb" role="img" aria-label="Author portrait"></div><p>Lorem Ipsum is simply<br>dummy text of<br>Today 5:60 pm-12.06.2016</p></div>
  </div>

  <div class="abs f-col news" style="left:342px;width:140px">
    <h4>Latest News</h4>
    <p>We only buy and renovate homes in our neighborhood</p>
    <p class="date">April 18th,2016</p>
    <a class="more" href="#">READ MORE <svg width="12" height="12" viewBox="0 0 14 14"><circle cx="7" cy="7" r="6.3" fill="none" stroke="currentColor"/><path d="M6 4l3 3-3 3" fill="none" stroke="currentColor"/></svg></a>
    <hr>
    <p>We are a team of experienced home buyers.</p>
    <p class="date">March 23rd,2016</p>
    <a class="more" href="#">READ MORE <svg width="12" height="12" viewBox="0 0 14 14"><circle cx="7" cy="7" r="6.3" fill="none" stroke="currentColor"/><path d="M6 4l3 3-3 3" fill="none" stroke="currentColor"/></svg></a>
  </div>

  <div class="abs f-col" style="left:514px;width:190px">
    <h4>Get In Touch with Us</h4>
    <ul class="reach">
      <li><svg width="12" height="13" viewBox="0 0 12 13"><path d="M6 0a4.5 4.5 0 00-4.5 4.5C1.5 8 6 13 6 13s4.5-5 4.5-8.5A4.5 4.5 0 006 0zm0 6.3a1.8 1.8 0 110-3.6 1.8 1.8 0 010 3.6z" fill="var(--teal)"/></svg><span>48 ALDER RIDGE RD<br>BROOKVALE,NJ 07000</span></li>
      <li><svg width="13" height="10" viewBox="0 0 13 10"><rect width="13" height="10" rx="1" fill="var(--teal)"/><path d="M0 1l6.5 4.5L13 1" fill="none" stroke="var(--footer)" stroke-width="1"/></svg><span>info@pinecrestholdingsgroup.example</span></li>
      <li><svg width="12" height="12" viewBox="0 0 12 12"><path d="M2 0l2.5.4 1 3-1.5 1.3a7 7 0 003.3 3.3L8.6 6.5l3 1 .4 2.5-2 1.8C4.8 11.8.2 7.2 0 2z" fill="var(--teal)"/></svg><span>555-013-7720</span></li>
      <li><svg width="13" height="13" viewBox="0 0 13 13"><rect x="0" y="3" width="4" height="10" fill="var(--teal)"/><rect x="5" y="0" width="8" height="13" fill="var(--teal)"/><rect x="7" y="2" width="4" height="3" fill="var(--footer)"/></svg><span>555-013-7720</span></li>
    </ul>
  </div>

  <div class="abs bottom-bar"><span>© PINECREST HOLDINGS GROUP</span>&nbsp;.2016 All Rights Reserved</div>
</footer>

</body>
</html>
```